I need a business card for my original fine art pieces

I would like a business card design including a logo design for a new business in the art world. I am based in the Hunter Valley NSW Australia. I am a contemporary figurative, encaustic and wildlife artist. I would like to be able to upload my email and mobile number to this as well. This design should be one that I can incorporate into banners and flyers etc. Id like to incorporate one of my own images or partial image into the background or somewhere below. My initials are RJ and I would like these used as a logo type. I would like the use of some colour and it to be bright and catchy. The final design should communicate artwork custom made and commissions available.

Overview: Original Fine Artworks for sale, online, art galleries etc, Custom made to order and by commission.

Target market is world wide audience and corporate world

My figurative work is painted using acrylics in a lot of natural ochre colours that reflect the Australian Outback, on canvas, linen, paper or board: My encaustic work is created in a contemporary abstract style using a blow torch and a made with a medium of 100% pure bees wax, Damar resin, mixed media and coloured pigments, applied to Birch board. My wildlife are created using coloured pencil and mixed media on a variety of paper types or board.

```html
<!DOCTYPE html>
<html lang="en">
<head>
<meta charset="utf-8">
<title>Rhea Jansen – Business Cards</title>
<link href="https://fonts.googleapis.com/css2?family=Cinzel:wght@400&family=Open+Sans:wght@400;600&family=Roboto:wght@400&display=swap" rel="stylesheet">
<style>
  :root {
    --ink: #000000;
    --flame: #ff4a00;
    --paper: #ffffff;
    --backdrop: #e9e7e4;
    --rule: rgba(255,255,255,0.35);
  }
  * { box-sizing: border-box; margin: 0; padding: 0; }
  html, body { width: 1200px; height: 900px; overflow: hidden; }
  body { background: var(--backdrop); position: relative; font-family: "Open Sans", sans-serif; }

  .card { position: absolute; overflow: hidden; box-shadow: 0 6px 18px rgba(0,0,0,0.18); }

  /* Brand mark: plain dot plus initials in the card's text font */
  .brand-mark {
    position: absolute; display: flex; align-items: center; gap: 14px;
    font-family: "Open Sans", sans-serif; font-weight: 600; color: var(--flame);
    line-height: 1;
  }
  .brand-mark__dot { border-radius: 50%; background: var(--flame); flex: none; }

  /* Front card */
  .card--front { left: 78px; top: 34px; width: 588px; height: 364px; background: var(--flame); }
  .card--front .top-band { position: absolute; left: 0; top: 0; width: 100%; height: 156px; background: var(--ink); }
  .card--front .brand-mark { left: 360px; top: 46px; font-size: 60px; }
  .card--front .brand-mark__dot { width: 34px; height: 34px; }

  .person { position: absolute; left: 30px; top: 172px; color: var(--paper); }
  .person__name { font-weight: 600; font-size: 19px; line-height: 1.2; }
  .person__role { font-size: 15px; line-height: 1.3; }

  .contacts { position: absolute; left: 0; top: 254px; width: 247px; list-style: none; }
  .contacts li {
    height: 31px; display: flex; align-items: center; gap: 10px;
    padding-left: 32px; color: var(--paper); font-size: 15px;
    border-bottom: 1px solid var(--rule);
  }
  .contacts li:last-child { border-bottom: none; }
  .contacts svg { width: 13px; height: 13px; fill: var(--paper); flex: none; }

  /* Back card */
  .card--back { left: 388px; top: 505px; width: 567px; height: 352px; background: var(--flame); }
  .card--back .mid-band { position: absolute; left: 0; top: 61px; width: 100%; height: 230px; background: var(--ink); }
  .card--back .brand-mark { left: 0; width: 100%; justify-content: center; top: 112px; font-size: 52px; }
  .card--back .brand-mark__dot { width: 28px; height: 28px; }
  .brand { position: absolute; left: 0; top: 212px; width: 100%; text-align: center; }
  .brand__name { font-family: "Cinzel", serif; font-size: 44px; color: var(--flame); line-height: 1.1; letter-spacing: 1px; }
  .brand__tagline { font-family: "Roboto", sans-serif; font-size: 19px; letter-spacing: 3.6px; color: var(--paper); line-height: 1.2; }
</style>
</head>
<body>

<section class="card card--front" aria-label="Business card front">
  <div class="top-band"></div>
  <div class="brand-mark">
    <span class="brand-mark__dot"></span>
    <span class="brand-mark__text">RJ</span>
  </div>
  <div class="person">
    <p class="person__name">Daniel Hart</p>
    <p class="person__role">Managing Director</p>
  </div>
  <ul class="contacts">
    <li>
      <svg viewBox="0 0 16 16" aria-hidden="true"><path d="M3.6 1.2l2.3 2.9-1.4 1.7c.9 2 2.4 3.6 4.4 4.6l1.7-1.4 2.9 2.3-1.4 2.9C6.6 14 2 9.4 1.5 2.6z"/></svg>
      044-987 654 321
    </li>
    <li>
      <svg viewBox="0 0 16 16" aria-hidden="true"><path d="M1 3h14v1.2L8 8.6 1 4.2z M1 5.8l7 4.4 7-4.4V13H1z"/></svg>
      hello@rjstudio.com
    </li>
    <li>
      <svg viewBox="0 0 16 16" aria-hidden="true"><path d="M6.5 9.5l3-3" stroke="#fff" stroke-width="1.6" fill="none"/><path d="M7 4.5l1.8-1.8a2.6 2.6 0 013.7 3.7L10.7 8.2M9 11.5l-1.8 1.8a2.6 2.6 0 01-3.7-3.7L5.3 7.8" stroke="#fff" stroke-width="1.6" fill="none"/></svg>
      www.rjstudio.com
    </li>
  </ul>
</section>

<section class="card card--back" aria-label="Business card back">
  <div class="mid-band"></div>
  <div class="brand-mark">
    <span class="brand-mark__dot"></span>
    <span class="brand-mark__text">RJ</span>
  </div>
  <div class="brand">
    <p class="brand__name">Rhea Jansen</p>
    <p class="brand__tagline">ORIGINAL FINE ARTWORKS</p>
  </div>
</section>

</body>
</html>
```